Landing Page for a new, High Production, farming technology

Brightfield Crate
We need a single landing page, with an email signup for more information.
We build self-contained, farming boxes out of ISO containers. These containers use hydroponics and LED lighting to provide a year round growing environment for crops. So, you could grow crops anywhere at any time of the year in any environment.
For the purpose of this site, we will be doing split testing between several different themes using different sites and keywords.
This site's focus should be providing our product to people searching for high production farming technology.
We'll be focusing on the following key words: Agriculture, aquaponics, farm, garden, hydroponics, organic food, subsistence farming, urban farming, vertical garden.
Target Market(s)
We are going to be using this page to judge that
Number of Pages Required
1 page
Look and feel
Each slider illustrates characteristics of the customer's brand and the style your logo design should communicate.

```html
<!DOCTYPE html>
<html lang="en">
<head>
<meta charset="utf-8">
<title>Brightfield Crate</title>
<link href="https://fonts.googleapis.com/css2?family=Poppins:wght@400;500;600;700&display=swap" rel="stylesheet">
<style>
:root{
  --header-bg:#f0f0f0;
  --footer-bg:#f8f8f8;
  --ink:#222;
  --orange:#e29a55;
  --green:#7fb069;
  --white:#fff;
  --photo-dark:#1e3340;
  --photo-mid:#2f5560;
  --photo-leaf:#4f7f52;
}
*{box-sizing:border-box;margin:0;padding:0}
html,body{width:1200px;height:1136px;overflow:hidden;font-family:"Poppins",sans-serif;color:var(--ink)}
.page{position:relative;width:1200px;height:1136px}
.site-header{position:absolute;top:0;left:0;width:1200px;height:90px;background:var(--header-bg)}
.brand{position:absolute;left:90px;top:27px;display:flex;align-items:center;gap:10px;font-size:19px;font-weight:500;color:var(--green);letter-spacing:1px}
.brand-square{width:30px;height:30px;background:var(--orange)}
.main-nav{position:absolute;left:432px;top:32px;display:flex;gap:27px;font-size:18px}
.main-nav a{color:var(--ink);text-decoration:none}
.header-signup{position:absolute;left:1025px;top:27px;width:100px;height:35px;border:2px solid var(--orange);border-radius:18px;color:var(--orange);font-weight:600;font-size:16px;display:flex;align-items:center;justify-content:center}
.hero{position:absolute;top:90px;left:0;width:1200px;height:920px;overflow:hidden}
.hero-photo{position:absolute;inset:0;background:radial-gradient(ellipse at 50% 55%,var(--photo-leaf) 0%,var(--photo-mid) 45%,var(--photo-dark) 100%)}
.hero-shapes{position:absolute;inset:0}
.hero-mark{position:absolute;left:548px;top:116px;width:104px;height:104px;border:10px solid var(--white)}
.hero-title{position:absolute;top:283px;width:100%;text-align:center;color:var(--white);font-size:54px;font-weight:700}
.slide-arrow{position:absolute;top:310px;width:32px;height:32px;border-radius:50%;background:#111;display:flex;align-items:center;justify-content:center}
.slide-arrow.prev{left:97px}.slide-arrow.next{left:1071px}
.signup-form{position:absolute;left:272px;top:364px;width:657px;height:64px;border:3px solid var(--white);border-radius:3px}
.signup-input{position:absolute;left:8px;top:8px;width:519px;height:41px;background:var(--white);border-radius:3px;font-size:12px;padding:13px 16px;color:#333}
.signup-button{position:absolute;left:539px;top:8px;width:104px;height:41px;background:var(--orange);border-radius:3px;color:var(--white);font-weight:600;font-size:16px;display:flex;align-items:center;justify-content:center}
.welcome-title{position:absolute;top:636px;width:100%;text-align:center;color:var(--white);font-size:42px;font-weight:700}
.welcome-text{position:absolute;top:706px;left:180px;width:840px;text-align:center;color:var(--white);font-size:13.6px;line-height:24px}
.read-more{position:absolute;left:535px;top:825px;width:131px;height:36px;border:2px solid var(--white);border-radius:18px;color:var(--white);font-weight:600;font-size:16px;display:flex;align-items:center;justify-content:center}
.site-footer{position:absolute;top:1010px;left:0;width:1200px;height:126px;background:var(--footer-bg)}
.social{position:absolute;top:34px;left:543px;display:flex;gap:3px}
.social span{width:26px;height:26px;border:1px solid #333;border-radius:50%}
.copyright{position:absolute;top:80px;width:100%;text-align:center;font-size:13px}
</style>
</head>
<body>
<div class="page">
  <header class="site-header">
    <div class="brand"><span class="brand-square"></span>Brightfield Crate</div>
    <nav class="main-nav"><a>Home</a><a>About</a><a>Products</a><a>Why Brightfield Crate?</a><a>Contact</a></nav>
    <div class="header-signup">SIGN UP</div>
  </header>
  <section class="hero">
    <div class="hero-photo" role="img" aria-label="Interior of a container farm with shelves of leafy greens under LED lights"></div>
    <svg class="hero-shapes" width="1200" height="920" viewBox="0 0 1200 920">
      <path d="M0,640 L40,639 Q600,501 1160,639 L1200,640 V920 H0Z" fill="#8fc17a" opacity="0.82"/>
      <path d="M40,639 Q600,501 1160,639" fill="none" stroke="#fff" stroke-width="3"/>
    </svg>
    <div class="hero-mark"></div>
    <h1 class="hero-title">Brightfield Crate</h1>
    <div class="slide-arrow prev"><svg width="14" height="14" viewBox="0 0 14 14"><path d="M9 2 L4 7 L9 12" stroke="#fff" stroke-width="2.5" fill="none"/></svg></div>
    <div class="slide-arrow next"><svg width="14" height="14" viewBox="0 0 14 14"><path d="M5 2 L10 7 L5 12" stroke="#fff" stroke-width="2.5" fill="none"/></svg></div>
    <div class="signup-form">
      <div class="signup-input">Enter your email</div>
      <div class="signup-button">SIGNUP</div>
    </div>
    <h2 class="welcome-title">welcome to brightfield crate</h2>
    <p class="welcome-text">Sed ut perspiciatis unde omnis iste natus error sit voluptatem accusantium doloremque laudantium, totam rem aperiam, eaque ipsa quae ab illo inventore veritatis et quasi architecto beatae vitae dicta sunt explicabo. Nemo enim ipsam voluptatem quia voluptas sit aspernatur aut odit aut fugit, sed quia consequuntur magni dolores eos qui ratione voluptatem sequi nesciunt. Neque porro quisquam est, qui dolorem ipsum quia dolor sit amet, consectetur, adipisci velit</p>
    <div class="read-more">Read More</div>
  </section>
  <footer class="site-footer">
    <div class="social"><span></span><span></span><span></span><span></span></div>
    <p class="copyright">© Copyright 2018 Brightfield Crate. All Rights Reserved.</p>
  </footer>
</div>
</body>
</html>
```